Web page design for a startup, no coding

Quorvix is a Data mining startup helping companies get data from websites. We’re looking to revamp our website to make it more professional and conversation friendly.
I need a designer to design the website in PSD and Once the PSD is done, the HTML design will be awarded as a separate job. We’ll need continues improvements to the design based on the user behaviour in the site and this can be a long term work for the right designer.
Read the details on the attached document
Target Market(s)
Big data, Data Mining
Industry/Entity Type
Business Software
Number of Pages Required
5+ page
Requirements
Must have
- Refer to the doc
Nice to have
- Refer to the doc
Should not have
- Refer to the doc

```html
<!DOCTYPE html>
<html lang="en">
<head>
<meta charset="utf-8">
<title>Quorvix – Turn Websites Into Structured Data Feeds</title>
<link rel="stylesheet" href="https://fonts.googleapis.com/css2?family=Open+Sans:wght@400;600;700&family=Oswald:wght@400;500&display=swap">
<style>
  :root {
    --ink: #222629;
    --text: #555b60;
    --nav: #2a4a6b;
    --green: #6aa557;
    --green-dark: #3b7a2e;
    --green-band: #3f7c33;
    --yellow: #f2b90f;
    --hero-deep: #0c2559;
    --hero-mid: #1f5aa8;
    --line: #cfd3d6;
    --white: #ffffff;
    --grey-icon: #8a8f93;
  }
  * { box-sizing: border-box; margin: 0; padding: 0; }
  html, body { width: 1200px; height: 2839px; overflow: hidden; }
  body { position: relative; background: var(--white); font-family: "Open Sans", Arial, sans-serif; color: var(--text); }
  .abs { position: absolute; }
  .center { left: 0; width: 1200px; text-align: center; }

  /* header */
  .site-header { top: 0; left: 0; width: 1200px; height: 110px; background: var(--white); }
  .brand { left: 89px; top: 32px; display: flex; align-items: center; gap: 12px; }
  .brand-mark { width: 34px; height: 34px; border: 3px solid var(--ink); }
  .brand-name { font-size: 34px; font-weight: 400; color: var(--ink); letter-spacing: -0.5px; }
  .main-nav { top: 48px; left: 577px; display: flex; gap: 0; }
  .main-nav a { font-size: 16px; color: var(--nav); text-decoration: none; text-transform: uppercase; position: absolute; white-space: nowrap; }

  /* hero */
  .hero { top: 110px; left: 0; width: 1200px; height: 528px;
    background: radial-gradient(ellipse at 60% 30%, #3d86d6 0%, var(--hero-mid) 30%, var(--hero-deep) 75%, #071634 100%); }
  .hero-title { top: 288px; font-family: "Oswald", "Arial Narrow", sans-serif; font-weight: 500; font-size: 38px; color: var(--white); letter-spacing: 0.3px; }
  .hero-sub { top: 338px; font-size: 19px; line-height: 30px; color: var(--white); }
  .btn-ghost { top: 432px; left: 494px; width: 222px; height: 53px; border: 2px solid var(--white); border-radius: 27px; color: var(--white); font-size: 20px; text-align: center; line-height: 49px; }

  /* section titles */
  .section-title { font-size: 31px; font-weight: 600; color: var(--green); text-transform: uppercase; letter-spacing: 0.5px; }
  .section-lead { font-size: 17px; line-height: 27px; color: var(--text); }

  /* offerings */
  .offer-card { top: 833px; width: 312px; height: 360px; background: var(--white); box-shadow: 0 2px 6px rgba(0,0,0,0.22); }
  .offer-media { width: 312px; height: 174px; }
  .offer-title { margin-top: 24px; text-align: center; font-size: 15px; font-weight: 600; color: var(--ink); letter-spacing: 0.4px; }
  .offer-text { margin: 10px 26px 0; text-align: center; font-size: 12.5px; line-height: 22.5px; color: var(--text); height: 68px; overflow: hidden; }
  .btn-small { display: block; margin: 12px auto 0; width: 102px; height: 29px; border: 1px solid #9aa0a4; border-radius: 15px; font-size: 12.5px; line-height: 27px; text-align: center; color: var(--ink); }
  .dots { top: 1232px; left: 567px; display: flex; gap: 8px; }
  .dots span { width: 15px; height: 15px; border-radius: 50%; background: #a6a6a6; }
  .dots span.active { background: var(--yellow); }

  /* why us */
  .why-band { top: 1287px; left: 0; width: 1200px; height: 441px; background: linear-gradient(100deg, #2f6e27 0%, var(--green-band) 50%, #4f8b3f 100%); }
  .why-title { top: 1350px; font-size: 31px; font-weight: 600; color: var(--white); }
  .why-item { width: 420px; color: var(--white); }
  .why-icon { position: absolute; left: -72px; top: 6px; }
  .why-item h3 { font-size: 17px; font-weight: 400; text-transform: uppercase; letter-spacing: 0.3px; }
  .why-item p { margin-top: 6px; font-size: 12.5px; line-height: 22px; height: 44px; overflow: hidden; }
  .why-item .more { display: block; margin-top: 4px; font-size: 12.5px; }

  /* contact */
  .field { border: 2px solid #d7dadc; background: var(--white); font-size: 15px; color: #6a6f73; padding-left: 24px; }
  .field-input { top: 1944px; height: 64px; width: 458px; line-height: 60px; }
  .field-area { top: 2029px; left: 127px; width: 939px; height: 161px; padding-top: 22px; }
  .select-caret { position: absolute; right: 30px; top: 27px; }
  .btn-submit { top: 2230px; left: 500px; width: 200px; height: 44px; border-radius: 22px; background: var(--green); color: var(--white); font-size: 16px; font-weight: 600; text-align: center; line-height: 44px; }

  /* testimonial */
  .testimonial { top: 2328px; left: 0; width: 1200px; height: 349px; background: linear-gradient(135deg, #f5c21e 0%, var(--yellow) 50%, #eeb000 100%); }
  .avatar { top: 2385px; left: 551px; width: 114px; height: 114px; border-radius: 50%; border: 4px solid var(--white); background: linear-gradient(160deg, #c98f66, #7b4a32); }
  .quote { top: 2514px; left: 180px; width: 840px; text-align: center; font-size: 15px; font-style: italic; line-height: 23px; color: var(--white); }
  .quote-by { top: 2598px; font-size: 15px; font-style: italic; color: var(--white); }

  /* footer */
  .footer-links { top: 2717px; font-size: 12px; font-weight: 600; color: var(--ink); letter-spacing: 0.3px; }
  .footer-links span.sep { margin: 0 10px; }
  .social { top: 2756px; left: 456px; display: flex; gap: 11px; }
  .social span { width: 21px; height: 21px; border-radius: 50%; background: var(--grey-icon); }
  .copyright { top: 2794px; font-size: 12px; color: var(--ink); }
</style>
</head>
<body>

<header class="site-header abs">
  <div class="brand abs"><span class="brand-mark"></span><span class="brand-name">quorvix</span></div>
  <nav class="main-nav abs">
    <a style="left:0">Solutions</a>
    <a style="left:148px">Pricing</a>
    <a style="left:270px">Company</a>
    <a style="left:405px">Get Free Quote</a>
  </nav>
</header>

<section class="hero abs" role="img" aria-label="Businessman touching a glowing digital data interface over a blue city grid"></section>
<h1 class="hero-title abs center">TURN WEBSITES INTO STRUCTURED DATA FEEDS</h1>
<p class="hero-sub abs center">Easily get structured data feeds from any website through our cloud based data<br>as a service platform. No programming ,Servers or Expensive Softwares required.</p>
<div class="btn-ghost abs">GET FREE QUOTE</div>

<h2 class="section-title abs center" style="top:690px">Our Offerings</h2>
<p class="section-lead abs center" style="top:738px">Businesses of all sizes use our clean data feeds to Quickly build apps, Experiment<br>with fresh ideas and Solve business problems.</p>

<article class="offer-card abs" style="left:87px">
  <div class="offer-media" role="img" aria-label="Hands holding floating product boxes" style="background:linear-gradient(135deg,#0d1f3d,#3d5e8c 55%,#0b1730)"></div>
  <h3 class="offer-title">ECOMMERCE</h3>
  <p class="offer-text">Our Ecommerce product data feeds gives you access to structured product information like pricing,, Category, reviews etc about your com-</p>
  <span class="btn-small">View More</span>
</article>
<article class="offer-card abs" style="left:443px">
  <div class="offer-media" role="img" aria-label="Hand touching a network of business icons" style="background:linear-gradient(135deg,#d5dde3,#8ea4b3 55%,#5f7888)"></div>
  <h3 class="offer-title">LEAD GENERATION</h3>
  <p class="offer-text">We help find quality leads for your business by extracting public data from all kind of sources like ProNet, FundBase, SeedRoll</p>
  <span class="btn-small">View More</span>
</article>
<article class="offer-card abs" style="left:799px">
  <div class="offer-media" role="img" aria-label="Businesswoman in front of a glowing world map" style="background:linear-gradient(135deg,#0a1a44,#2456b8 55%,#0b1d52)"></div>
  <h3 class="offer-title">SERP TRACKING</h3>
  <p class="offer-text">Our SERP data feeds gives companies access to Search Engine rankings of any keywords from search engines like Searchly, Findora and Lookr.</p>
  <span class="btn-small">View More</span>
</article>

<div class="dots abs"><span class="active"></span><span></span><span></span></div>

<section class="why-band abs" aria-label="Why us"></section>
<h2 class="why-title abs center">WHY US</h2>

<div class="why-item abs" style="left:159px;top:1440px">
  <svg class="why-icon" width="42" height="46" viewBox="0 0 42 46"><path d="M4 2h24l10 10v32H4z" fill="#fff"/><path d="M28 2v10h10" fill="#d9e6d4"/><path d="M10 20h22M10 27h22M10 34h16" stroke="#3f7c33" stroke-width="3"/></svg>
  <h3>Solve Real Problems</h3>
  <p>Quorvix provides a fully managed Big Data As A Service .You can easily plug our data feeds into your favourite tool and start solving</p>
  <span class="more">Read More »</span>
</div>
<div class="why-item abs" style="left:716px;top:1440px">
  <svg class="why-icon" width="46" height="46" viewBox="0 0 46 46"><rect x="3" y="9" width="32" height="32" rx="4" fill="none" stroke="#fff" stroke-width="4"/><path d="M18 30l2-8L38 4l6 6-18 18z" fill="#fff"/></svg>
  <h3>Clean Data</h3>
  <p>We follow a strict quality assurance process and a Machine learning based Q&amp;A system to ensure the data integrity. You can export data</p>
  <span class="more">Read More »</span>
</div>
<div class="why-item abs" style="left:159px;top:1569px">
  <svg class="why-icon" width="52" height="42" viewBox="0 0 52 42"><circle cx="26" cy="10" r="8" fill="#fff"/><circle cx="10" cy="14" r="6" fill="#fff"/><circle cx="42" cy="14" r="6" fill="#fff"/><path d="M12 40c0-12 6-18 14-18s14 6 14 18z" fill="#fff"/><path d="M0 38c0-9 4-14 10-14 3 0 5 1 6 3-3 3-5 7-5 11z" fill="#fff"/><path d="M52 38c0-9-4-14-10-14-3 0-5 1-6 3 3 3 5 7 5 11z" fill="#fff"/></svg>
  <h3>Customer Success</h3>
  <p>Ensuring Customer success is our first priority. Our customer success team consists experienced data mining engineers and they</p>
  <span class="more">Read More »</span>
</div>
<div class="why-item abs" style="left:716px;top:1569px">
  <svg class="why-icon" width="48" height="44" viewBox="0 0 48 44"><rect x="2" y="2" width="44" height="30" rx="2" fill="#fff"/><rect x="20" y="32" width="8" height="6" fill="#fff"/><rect x="12" y="38" width="24" height="4" fill="#fff"/></svg>
  <h3>Data Wrangling Support</h3>
  <p>Quorvix helps those who need data wrangling support by providing profiling, filtering and enrichment support. We know just getting</p>
  <span class="more">Read More »</span>
</div>

<h2 class="section-title abs center" style="top:1786px">We’re Here To Help!</h2>
<p class="section-lead abs center" style="top:1834px">We’re friendly and available to help solve your data extraction<br>problems. Fill the form below to contact us. Let us do the heavy lifting for you</p>

<form>
  <div class="field field-input abs" style="left:127px">Your Email address</div>
  <div class="field field-input abs" style="left:608px">Your Monthly Budget
    <svg class="select-caret" width="12" height="7" viewBox="0 0 12 7"><path d="M0 0h12L6 7z" fill="#555"/></svg>
  </div>
  <div class="field field-area abs">Drop us a line or two, We will get back to you Soon...</div>
  <div class="btn-submit abs">SUBMIT MESSAGE</div>
</form>

<section class="testimonial abs" aria-label="Customer testimonial"></section>
<svg class="abs" style="left:478px;top:2428px" width="16" height="28" viewBox="0 0 16 28"><path d="M14 2L3 14l11 12" fill="none" stroke="#fff" stroke-width="3"/></svg>
<svg class="abs" style="left:718px;top:2428px" width="16" height="28" viewBox="0 0 16 28"><path d="M2 2l11 12L2 26" fill="none" stroke="#fff" stroke-width="3"/></svg>
<div class="avatar abs" role="img" aria-label="Portrait of the reviewer"></div>
<p class="quote abs">“Quorvix was very responsive and quick to deliver. They were happy to do 2 iterations on the initial data scrape set up to ensure we got the info we needed moving forward. They delivered great results were others had previously failed. We’re excited to have found this service and will be looking ”</p>
<p class="quote-by abs center">Mara Lentz - Director of Business Development @ LaunchWell</p>

<footer>
  <p class="footer-links abs center">BLOG<span class="sep">|</span>ANSWERS<span class="sep">|</span>CASE STUDIES<span class="sep">|</span>SLIDE<span class="sep">|</span>FAQ<span class="sep">|</span>CAREERS<span class="sep">|</span>STARTUP PARTNER PROGRAM</p>
  <div class="social abs" aria-label="Social links"><span></span><span></span><span></span><span></span><span></span><span></span><span></span><span></span></div>
  <p class="copyright abs center">Copyright © 2016 All Rights Reserved</p>
</footer>

</body>
</html>
```